Request for Business Card Design

Hi. My name is Marlene, I am looking for a new business card design for my company, Quarrow Signal Instruments, LLC. I really like the design you did for Tarsel Venture and was hoping you could do something similar using our full logo and our mark. I am also open to any raised texture design using our mark. I have attached our full logo, which would need to be somewhere on the card, as well as the mark in both outline and full form, as well as our brand colors / guide. The card does not have to be white, as long as our logo and mark appear. I actually like darker colored business cards more, but am open to all options. If you are interested in working with me, please let me know. We would also take the business card design into letterhead design if you can do that.

```html
<!DOCTYPE html>
<html lang="en">
<head>
<meta charset="utf-8">
<title>Quarrow Signal Instruments — Business Card</title>
<link href="https://fonts.googleapis.com/css2?family=Barlow:wght@600&family=Roboto:wght@400;700&display=swap" rel="stylesheet">
<style>
  :root {
    --card-dark: #1f1f1f;
    --brand-blue: #0a9bc4;
    --ink-light: #ffffff;
    --stage: #e4e4e4;
  }
  * { margin: 0; padding: 0; box-sizing: border-box; }
  html, body { width: 1093px; height: 1200px; overflow: hidden; }
  body { background: var(--stage); position: relative; font-family: "Roboto", sans-serif; color: var(--ink-light); }

  .card {
    position: absolute;
    background: var(--card-dark);
    border-radius: 24px;
    overflow: hidden;
  }
  .card--front { left: 265px; top: 226px; width: 577px; height: 357px; }
  .card--back  { left: 266px; top: 620px; width: 580px; height: 359px; }

  .wordmark { font-family: "Barlow", sans-serif; font-weight: 600; color: var(--ink-light); position: absolute; line-height: 1; }
  .wordmark__name { display: block; letter-spacing: 4px; }
  .wordmark__line { display: block; letter-spacing: 0.6px; }

  .card--front .wordmark { left: 0; right: 0; top: 48px; text-align: center; }
  .card--front .wordmark__name { font-size: 50px; }
  .card--front .wordmark__line { font-size: 15px; margin-top: 5px; }

  .band { position: absolute; left: 0; top: 0; width: 577px; height: 357px; }

  .contact { position: absolute; right: 28px; top: 160px; text-align: right; }
  .contact__name { font-weight: 700; font-size: 24px; line-height: 1; letter-spacing: 0.2px; }
  .contact__role { font-size: 17px; line-height: 1; margin-top: 4px; letter-spacing: 0.3px; }
  .contact__list { list-style: none; margin-top: 17px; }
  .contact__item { font-size: 17px; line-height: 21px; display: flex; justify-content: flex-end; align-items: center; gap: 5px; letter-spacing: 0.2px; }
  .contact__icon { width: 15px; height: 15px; flex: none; }
  .contact__address { font-size: 17px; line-height: 21px; margin-top: 12px; letter-spacing: 0.2px; }

  .card--back .brand-dot { position: absolute; left: 117px; top: 142px; width: 74px; height: 74px; border-radius: 50%; background: var(--brand-blue); }
  .card--back .wordmark { left: 228px; top: 149px; }
  .card--back .wordmark__name { font-size: 51px; }
  .card--back .wordmark__line { font-size: 15.5px; margin-top: 6px; }
</style>
</head>
<body>

<section class="card card--front" aria-label="Business card front">
  <div class="wordmark">
    <span class="wordmark__name">QUARROW</span>
    <span class="wordmark__line">SIGNAL INSTRUMENTS</span>
  </div>

  <svg class="band" viewBox="0 0 577 357" aria-hidden="true">
    <rect x="0" y="153" width="577" height="204" fill="var(--brand-blue)"/>
    <path d="M0 150 H144 A106 106 0 0 1 144 357 H0 Z" fill="var(--card-dark)"/>
  </svg>

  <div class="contact">
    <p class="contact__name">ELIAS BRANDT</p>
    <p class="contact__role">Managing Director</p>
    <ul class="contact__list">
      <li class="contact__item">044-310 742 615
        <svg class="contact__icon" viewBox="0 0 16 16" aria-hidden="true"><path d="M4 1.5 L6 4.5 L4.8 6 C5.6 7.8 7.6 9.9 9.6 10.8 L11 9.6 L14.2 11.6 L13 14.3 C7 14 2 9 1.7 3 Z" fill="none" stroke="#fff" stroke-width="1.5" stroke-linejoin="round"/><path d="M9.5 2.5 A4.5 4.5 0 0 1 13.5 6.5 M9.5 5 A2 2 0 0 1 11 6.5" fill="none" stroke="#fff" stroke-width="1.3"/></svg>
      </li>
      <li class="contact__item">info@quarrowsignal.com
        <svg class="contact__icon" viewBox="0 0 16 16" aria-hidden="true"><rect x="1" y="3.5" width="14" height="9.5" fill="#fff"/><path d="M1 3.5 L8 9 L15 3.5 M1 13 L6 8 M15 13 L10 8" fill="none" stroke="var(--brand-blue)" stroke-width="1.2"/></svg>
      </li>
      <li class="contact__item">www.quarrowsignal.com
        <svg class="contact__icon" viewBox="0 0 16 16" aria-hidden="true"><g fill="none" stroke="#fff" stroke-width="1.3"><circle cx="8" cy="8" r="6.7"/><ellipse cx="8" cy="8" rx="3" ry="6.7"/><path d="M1.3 8 H14.7 M2.5 4.5 H13.5 M2.5 11.5 H13.5"/></g></svg>
      </li>
    </ul>
    <p class="contact__address">421, Address line goes here<br>45452,Country Name</p>
  </div>
</section>

<section class="card card--back" aria-label="Business card back">
  <span class="brand-dot" aria-hidden="true"></span>
  <div class="wordmark">
    <span class="wordmark__name">QUARROW</span>
    <span class="wordmark__line">SIGNAL INSTRUMENTS</span>
  </div>
</section>

</body>
</html>
```